Business card - Harbor Crest Builders

Design a business card utilizing the given logo.
colors we like: Black, greys, Teal, blues.
Tri color card, horizontal orientation likely
Logo and name likely best on top.
Info on card:

Dennis Farrow
#8 - 4815 Alder Ridge Blvd.
Surrey, B.C. V3K 2R9

778.555.0193
dennisfarrow@tellmail.ca

Slogan: "Building Dreams"

We are a construction company that specializes in new home construction on the West coast of BC Canada. Open Concepts designs of high end homes.

```html
<!DOCTYPE html>
<html lang="en">
<head>
<meta charset="utf-8">
<title>Harbor Crest Builders – Business Card</title>
<link rel="stylesheet" href="https://fonts.googleapis.com/css2?family=Mulish:wght@400;600;800&display=swap">
<style>
  :root {
    --page: #e4e4e2;
    --card-light: #ffffff;
    --card-shade: #e6e6e6;
    --ink: #1a1a1a;
    --ink-soft: #3a3a3a;
    --teal: #137f88;
    --teal-dark: #0f6a72;
    --strip: #cfcfcf;
  }
  * { box-sizing: border-box; margin: 0; padding: 0; }
  html, body {
    width: 1200px; height: 871px; overflow: hidden;
    background: var(--page);
    font-family: "Mulish", "Century Gothic", sans-serif;
    color: var(--ink);
  }
  .sheet {
    width: 1200px; height: 871px;
    display: flex; align-items: center; justify-content: center; gap: 40px;
  }
  .card {
    position: relative;
    width: 560px; height: 320px;
    background: linear-gradient(160deg, var(--card-light) 0%, var(--card-light) 45%, var(--card-shade) 100%);
    box-shadow: 0 6px 18px rgba(0,0,0,0.18);
    overflow: hidden;
  }
  .brand {
    display: flex; align-items: center; gap: 14px;
  }
  .brand-mark {
    width: 44px; height: 44px; border-radius: 50%;
    background: var(--ink); flex: none;
  }
  .brand-name {
    font-weight: 400; text-transform: uppercase;
    color: var(--ink); letter-spacing: 1px; line-height: 1;
  }

  /* Front */
  .card--front .brand {
    position: absolute; left: 0; right: 0; top: 92px; justify-content: center;
  }
  .card--front .brand-name { font-size: 27px; }
  .slogan-band {
    position: absolute; left: 0; right: 0; top: 222px; height: 38px;
    background: linear-gradient(90deg, var(--teal-dark), var(--teal));
    display: flex; align-items: center; justify-content: center;
    color: #fff; font-size: 15px; letter-spacing: 2px; font-weight: 600;
  }
  .base-strip {
    position: absolute; left: 0; right: 0; top: 260px; bottom: 0;
    background: var(--strip);
  }

  /* Back */
  .card--back .brand { position: absolute; left: 44px; top: 40px; }
  .card--back .brand-name { font-size: 26px; }
  .contact { position: absolute; left: 150px; top: 138px; }
  .contact-name {
    font-weight: 800; font-size: 14px; letter-spacing: 2.5px; margin-bottom: 18px;
  }
  .contact-address {
    font-size: 11.5px; letter-spacing: 1.6px; line-height: 1.5; color: var(--ink-soft);
    margin-bottom: 14px;
  }
  .contact-line {
    display: flex; align-items: center; gap: 10px;
    font-size: 11.5px; letter-spacing: 1.6px; color: var(--ink-soft); margin-bottom: 5px;
  }
  .contact-icon { width: 12px; height: 12px; flex: none; }
</style>
</head>
<body>
<main class="sheet">
  <section class="card card--front" aria-label="Card front">
    <div class="brand">
      <span class="brand-mark"></span>
      <span class="brand-name">Harbor Crest Builders</span>
    </div>
    <div class="slogan-band">Building Dreams</div>
    <div class="base-strip"></div>
  </section>

  <section class="card card--back" aria-label="Card back">
    <div class="brand">
      <span class="brand-mark"></span>
      <span class="brand-name">Harbor Crest Builders</span>
    </div>
    <div class="contact">
      <p class="contact-name">Dennis Farrow</p>
      <p class="contact-address">#8 - 4815 Alder Ridge Blvd.<br>Surrey, B.C. V3K 2R9</p>
      <p class="contact-line">
        <svg class="contact-icon" viewBox="0 0 12 12" aria-hidden="true">
          <path d="M1 4 Q6 0 11 4 L9.5 5.5 L8 4.2 L4 4.2 L2.5 5.5 Z" fill="var(--teal)"/>
          <rect x="2.5" y="6" width="7" height="5" rx="1" fill="none" stroke="var(--teal)" stroke-width="1.2"/>
        </svg>
        <span>778.555.0193</span>
      </p>
      <p class="contact-line">
        <svg class="contact-icon" viewBox="0 0 12 12" aria-hidden="true">
          <rect x="0.8" y="2.5" width="10.4" height="7" fill="none" stroke="var(--teal)" stroke-width="1.2"/>
          <path d="M0.8 2.5 L6 6.5 L11.2 2.5" fill="none" stroke="var(--teal)" stroke-width="1.2"/>
        </svg>
        <span>dennisfarrow@tellmail.ca</span>
      </p>
    </div>
  </section>
</main>
</body>
</html>
```